Business card for Crestline Bathrooms

Please design a business card for our bathroom renovation business. You can use my existing logo, but if you have an idea to modernize it, I would like to see it. Please see attached files first. I would like to use the blue and the orange theme. I like the concept of using the shower head in the logo. Please find following a design (or two) that I have been trying to create with my limited resources. That design was for a sign, but I was going to adopt it and use it as a business card as well. I like the concept of the water splash but I don’t think it “flows” nicely together with the logo. Another thought is that maybe creating the logo out of water splash could work and have a dramatic effect (like the water text and the butterfly picture attached with similar background instead of white). If the above doesn’t work I would like to see a modern simplified design. One of the attached files named as the unwanted business card has all the details that I want included in the business card. Please note that it is two sided.
Updates

I am very thankful for the designs that I have received, but they are very similar and only a couple of attempts to do something with the water splash as per my original brief. Modernizing the logo and having it made out of out of water splash with the orange as color accent could work and have a dramatic effect (like the water text and the butterfly picture attached with similar background instead of white). Please do not use the butterfly itself! This is just an example that images can be created out of water splash.

Contact Information for Business Card

all the details are on the unwonted business card file included

Colors
3176b5

Requirements
Nice to have
• Copied from the brief:
• ... maybe creating the logo out of water splash could work and have a dramatic effect (like the water text and the butterfly picture attached with similar background instead of white). Please do not use the butterfly itself!
Should not have
• I am getting designs with a butterfly. The butterfly picture was an example of creating something from a water splash. The butterfly itself has no association with anything other than the concept of creating a logo out of water splash. Sorry, I thought I was clear in the brief.

```html
<!DOCTYPE html>
<html lang="en">
<head>
<meta charset="utf-8">
<title>Crestline Bathrooms – Business Card</title>
<link rel="stylesheet" href="https://fonts.googleapis.com/css2?family=Arimo:wght@400;700&display=swap">
<style>
  :root {
    --navy: #0f4170;
    --coral: #e8766a;
    --water-light: #e6f2fb;
    --water-mid: #b9d8ee;
    --water-deep: #8fbcdc;
    --paper: #ffffff;
    --backdrop: #eceef0;
    --ink: #1c2a38;
  }
  * { box-sizing: border-box; margin: 0; padding: 0; }
  html, body { width: 1200px; height: 900px; overflow: hidden; }
  body {
    background: var(--backdrop);
    font-family: "Arimo", Arial, sans-serif;
    position: relative;
  }
  .card {
    position: absolute;
    width: 540px;
    height: 310px;
    background: var(--paper);
    overflow: hidden;
    box-shadow: 0 6px 18px rgba(0,0,0,0.18);
  }
  .card--back { left: 90px; top: 130px; }
  .card--front { left: 570px; top: 450px; }

  /* Back side */
  .splash {
    position: absolute; inset: 0;
    background:
      radial-gradient(ellipse 60% 35% at 40% 62%, var(--water-deep), transparent 70%),
      linear-gradient(180deg, var(--water-light) 0%, var(--water-mid) 70%, var(--water-light) 100%);
  }
  .brand {
    position: absolute;
    display: flex; align-items: center; gap: 10px;
    color: var(--navy);
    font-weight: 700;
    line-height: 1;
  }
  .brand__dot {
    width: 16px; height: 16px; border-radius: 50%;
    background: var(--coral);
    flex: none;
  }
  .brand__name span { display: block; }
  .card--back .brand { right: 28px; top: 26px; font-size: 30px; }
  .card--back .brand__name span + span { font-size: 20px; margin-top: 4px; }
  .services {
    position: absolute; left: 30px; bottom: 44px;
    list-style: none;
    color: var(--navy);
    font-weight: 700;
    font-size: 16px;
    line-height: 1.35;
  }
  .services li::before {
    content: ""; display: inline-block;
    width: 8px; height: 8px; border-radius: 50%;
    background: var(--navy);
    margin-right: 8px; vertical-align: middle;
  }

  /* Front side */
  .person {
    position: absolute; left: 32px; top: 56px;
    font-weight: 700; font-size: 19px; letter-spacing: 0.5px;
    color: var(--navy);
  }
  .person__surname { color: var(--coral); }
  .card--front .brand { right: 26px; top: 26px; font-size: 32px; }
  .card--front .brand__name span + span { font-size: 21px; margin-top: 4px; }
  .contact {
    position: absolute; left: 32px; top: 118px;
    list-style: none;
    font-size: 15px; line-height: 1.3;
    color: var(--ink);
    z-index: 1;
  }
  .contact li { display: flex; align-items: center; gap: 7px; }
  .contact svg { width: 12px; height: 12px; fill: var(--navy); flex: none; }
  .postal { margin-top: 6px; font-size: 16px; }
  .wave { position: absolute; left: 0; top: 0; width: 540px; height: 310px; }
  .badge {
    position: absolute;
    background: var(--paper);
  }
  .badge--builders { right: 110px; bottom: 60px; width: 46px; height: 34px; }
  .badge--association { right: 22px; bottom: 100px; width: 40px; height: 48px; border-radius: 6px; }
</style>
</head>
<body>

  <section class="card card--back" aria-label="Card back">
    <div class="splash" role="img" aria-label="Light blue water splash photograph"></div>
    <div class="brand">
      <span class="brand__dot"></span>
      <div class="brand__name"><span>Crestline</span><span>Bathrooms</span></div>
    </div>
    <ul class="services">
      <li>Complete bathroom renovations &amp; remodelling</li>
      <li>Highly skilled &amp; qualified tradespeople</li>
      <li>Professional service from concept to completion</li>
      <li>All work guaranteed</li>
    </ul>
  </section>

  <section class="card card--front" aria-label="Card front">
    <p class="person">PETER <span class="person__surname">MAROVSKI</span></p>
    <div class="brand">
      <span class="brand__dot"></span>
      <div class="brand__name"><span>Crestline</span><span>Bathrooms</span></div>
    </div>
    <ul class="contact">
      <li><svg viewBox="0 0 12 12"><path d="M1 4c0-2 2-3 5-3s5 1 5 3v1H8V4H4v1H1zM2 6h8l1 5H1z"/></svg>0400 555 012</li>
      <li><svg viewBox="0 0 12 12"><path d="M3 0h6a1 1 0 0 1 1 1v10a1 1 0 0 1-1 1H3a1 1 0 0 1-1-1V1a1 1 0 0 1 1-1zm0 2v7h6V2z"/></svg>6200 5550</li>
      <li><svg viewBox="0 0 12 12"><path d="M0 2h12v8H0zm1 1v.5l5 3.5 5-3.5V3z"/></svg>peter@crestlinebathrooms.com.au</li>
      <li><svg viewBox="0 0 12 12"><circle cx="6" cy="6" r="6"/></svg>crestlinebathrooms.com.au</li>
      <li class="postal">PO Box 41 Larchwood 2600</li>
    </ul>
    <svg class="wave" viewBox="0 0 540 310" aria-hidden="true">
      <path d="M0 256 C150 250 290 226 400 168 C300 232 150 264 0 274 Z" fill="var(--coral)"/>
      <path d="M0 282 C180 272 330 238 430 170 C470 144 510 130 540 126 L540 310 L0 310 Z" fill="var(--navy)"/>
    </svg>
    <div class="badge badge--builders" aria-label="Builders association membership badge"></div>
    <div class="badge badge--association" aria-label="Industry association membership badge"></div>
  </section>

</body>
</html>
```